Presentation Of Our Epidemiology Consulting Framework

We need a slide deck (png files) for PowerPoint that describes our organization and type of clients we serve, and our 6 phase framework that explains how we work with clients. Please use the minimum amount of text on each slide.  We want a more visual display of how to work with us. We want it to look very similar to our brochure.  We want to also have a few extra branded slides without text that can be used as a template if we decide to add to the deck later or create a new slide deck.
Colors
#56588C
#F28444
#F2E088
#F24C27
#ODODOD

```html
<!DOCTYPE html>
<html lang="en">
<head>
<meta charset="utf-8">
<title>The DrAVance Framework – Slide Deck</title>
<link href="https://fonts.googleapis.com/css2?family=Montserrat:wght@500;600;700;800&display=swap" rel="stylesheet">
<style>
  :root{
    --indigo:#56588C;
    --indigo-soft:#4f4d8a;
    --ink:#13122e;
    --night:#0f0f2a;
    --lilac:#6c68b2;
    --orange:#F28444;
    --flame:#F24C27;
    --canvas:#fde9e1;
    --pill:#fdf0ea;
    --white:#ffffff;
    --text:#0D0D0D;
  }
  *{box-sizing:border-box;margin:0;padding:0}
  html,body{width:1200px;height:1065px;overflow:hidden}
  body{background:var(--canvas);font-family:"Montserrat",sans-serif;position:relative}
  .slide{position:absolute;width:548px;height:308px;background:var(--white);overflow:hidden;box-shadow:0 4px 14px rgba(242,132,68,.18)}
  .slide svg.backdrop{position:absolute;left:0;top:0;width:548px;height:308px}
  .s1{left:36px;top:32px}.s2{left:619px;top:32px}
  .s3{left:36px;top:379px}.s4{left:622px;top:379px}
  .s5{left:36px;top:721px}.s6{left:622px;top:721px}

  .phase-title{position:absolute;left:0;width:100%;top:14px;text-align:center;color:var(--white);font-weight:700;font-size:16px;letter-spacing:.2px}
  .subtitle{position:absolute;left:0;width:100%;text-align:center;color:var(--text);font-weight:700;font-size:13.5px}

  /* footer */
  .brand-mini{position:absolute;left:27px;top:278px;font-weight:700;font-size:15px;color:var(--indigo);display:flex;align-items:center;gap:5px}
  .brand-mini .dot{width:9px;height:9px;border-radius:50%;background:var(--orange)}
  .rule{position:absolute;left:160px;top:287px;width:388px;height:1.5px;background:var(--orange)}
  .rule::before{content:"";position:absolute;left:-3px;top:-2.5px;width:6px;height:6px;border-radius:50%;background:var(--flame)}
  .page-no{position:absolute;right:17px;top:278px;width:20px;height:20px;border-radius:50%;background:var(--flame);color:var(--text);font-size:8px;font-weight:700;display:flex;align-items:center;justify-content:center}

  /* cover */
  .cover-title{position:absolute;left:26px;top:24px;font-weight:800;font-size:19.5px;line-height:32px;color:var(--white)}
  .cover-title .accent{color:var(--orange)}
  .portrait{position:absolute;left:352px;top:0;width:196px;height:185px;background:radial-gradient(ellipse at 55% 40%,#5a4a52 0%,#3c3560 45%,rgba(80,76,150,0) 75%)}
  .brand-hero{position:absolute;left:0;width:100%;top:233px;display:flex;justify-content:center;align-items:center;gap:10px;font-weight:700;font-size:38px;color:var(--indigo)}
  .brand-hero .dot{width:22px;height:22px;border-radius:50%;background:var(--orange)}

  /* step cards */
  .card{position:absolute;width:109px;color:var(--white);font-size:7.6px;font-weight:500;line-height:14px;text-align:center;border-radius:3px;padding:0 6px}
  .card.dark{background:var(--ink)}
  .card.mid{background:var(--indigo-soft)}
  .badge{display:block;width:52px;height:22px;margin:0 auto 10px;border-radius:0 0 26px 26px;background:var(--flame);font-size:12.5px;font-weight:700;line-height:20px;color:var(--white)}

  /* circles */
  .orb{position:absolute;top:161px;width:82px;height:82px;border-radius:50%;background:radial-gradient(circle at 70% 40%,var(--lilac) 0%,#3a3670 50%,var(--night) 100%);color:var(--white);font-size:9.6px;font-weight:600;line-height:16px;text-align:center;display:flex;align-items:center;justify-content:center;padding:0 3px;white-space:nowrap}
  .orb::after{content:"";position:absolute;inset:-7px;border-radius:50%;border:3px solid transparent}
  .orb.arc-top::after{border-top-color:var(--flame);border-right-color:var(--flame);transform:rotate(-20deg)}
  .orb.arc-bottom::after{border-bottom-color:var(--flame);border-left-color:var(--flame);transform:rotate(-20deg)}

  /* execution pills */
  .exec-sub{position:absolute;left:0;width:100%;text-align:center;color:var(--white);font-size:10px;font-weight:600}
  .pill{position:absolute;width:103px;height:138px;border-radius:52px;background:var(--pill);border:4px solid var(--white);box-shadow:0 2px 6px rgba(0,0,0,.05);overflow:hidden;text-align:center;color:var(--text);font-size:11.5px;line-height:19.5px}
  .pill .cap{display:block;height:40px;background:var(--flame);border-radius:0 0 50px 50px;color:var(--white);font-weight:700;font-size:16px;line-height:30px;margin-bottom:10px}
</style>
</head>
<body>

<!-- Slide 1: cover -->
<section class="slide s1">
  <svg class="backdrop" viewBox="0 0 548 308" aria-hidden="true">
    <defs><linearGradient id="band1" x1="0" x2="1" y1="0" y2="0"><stop offset="0" stop-color="#0f0f2a"/><stop offset="1" stop-color="#6c68b2"/></linearGradient></defs>
    <path d="M0 0H548V155C440 210 290 200 170 192C100 188 45 192 0 204Z" fill="url(#band1)"/>
    <path d="M25 210C110 186 230 192 320 206C410 220 490 200 548 158C500 210 420 240 320 236C220 232 120 214 25 210Z" fill="#F28444"/>
  </svg>
  <div class="portrait" role="img" aria-label="Portrait photograph of the founder"></div>
  <h1 class="cover-title">TRANSFORMING HEALTH DATA<br>INTO COMMUNITY IMPACT:<br><span class="accent">THE DRAVANCE<br>FRAMEWORK</span></h1>
  <div class="brand-hero"><span class="dot"></span>Dr AVance</div>
</section>

<!-- Slide 2: phase 1 -->
<section class="slide s2">
  <svg class="backdrop" viewBox="0 0 548 308" aria-hidden="true">
    <defs><linearGradient id="band2" x1="0" x2="1"><stop offset="0" stop-color="#0f0f2a"/><stop offset="1" stop-color="#6c68b2"/></linearGradient></defs>
    <path d="M0 0H548V45C450 85 330 80 230 74C150 70 70 66 0 80Z" fill="url(#band2)"/>
    <path d="M25 70C120 52 230 66 330 78C420 88 480 80 510 65C470 95 400 100 320 95C220 89 120 74 25 70Z" fill="#F28444"/>
  </svg>
  <h2 class="phase-title">PHASE 1: DISCOVERY &amp; VISION ALIGNMENT</h2>
  <p class="subtitle" style="top:112px">Building the Foundation for Success</p>
  <div class="card dark" style="left:27px;top:148px;height:106px"><span class="badge">01</span>Deep-dive exploration of your organization's unique challenges and opportunities</div>
  <div class="card mid" style="left:156px;top:148px;height:106px"><span class="badge">02</span>Strategic alignment of goals and expectations</div>
  <div class="card dark" style="left:284px;top:148px;height:106px"><span class="badge">03</span>Custom-tailored solution design</div>
  <div class="card mid" style="left:412px;top:148px;height:106px"><span class="badge">04</span>Clear roadmap development with defined milestones</div>
  <div class="brand-mini"><span class="dot"></span>Dr AVance</div><div class="rule"></div><div class="page-no">02</div>
</section>

<!-- Slide 3: phase 2 -->
<section class="slide s3">
  <svg class="backdrop" viewBox="0 0 548 308" aria-hidden="true">
    <defs><linearGradient id="band3" x1="0" x2="1"><stop offset="0" stop-color="#0f0f2a"/><stop offset="1" stop-color="#6c68b2"/></linearGradient></defs>
    <path d="M0 0H548V45C450 85 330 80 230 74C150 70 70 66 0 80Z" fill="url(#band3)"/>
    <path d="M25 70C120 52 230 66 330 78C420 88 480 80 510 65C470 95 400 100 320 95C220 89 120 74 25 70Z" fill="#F28444"/>
  </svg>
  <h2 class="phase-title">PHASE 2: PARTNERSHIP LAUNCH</h2>
  <p class="subtitle" style="top:112px">Setting the Stage for Excellence</p>
  <div class="orb arc-top" style="left:26px"><span>Formation<br>of dedicated<br>project<br>team</span></div>
  <div class="orb arc-bottom" style="left:132px"><span>Establish<br>ment of<br>collaborative<br>workflow</span></div>
  <div class="orb arc-top" style="left:231px"><span>Compreh<br>ensive<br>data<br>gathering</span></div>
  <div class="orb arc-bottom" style="left:336px"><span>Strategic<br>timeline<br>planning</span></div>
  <div class="orb arc-top" style="left:436px"><span>Formation<br>of dedicated<br>project<br>team</span></div>
  <div class="brand-mini"><span class="dot"></span>Dr AVance</div><div class="rule"></div><div class="page-no">03</div>
</section>

<!-- Slide 4: blank branded template -->
<section class="slide s4">
  <svg class="backdrop" viewBox="0 0 548 308" aria-hidden="true">
    <defs><linearGradient id="band4" x1="0" x2="1"><stop offset="0" stop-color="#0f0f2a"/><stop offset="1" stop-color="#6c68b2"/></linearGradient></defs>
    <path d="M0 0H548V45C450 85 330 80 230 74C150 70 70 66 0 80Z" fill="url(#band4)"/>
    <path d="M25 70C120 52 230 66 330 78C420 88 480 80 510 65C470 95 400 100 320 95C220 89 120 74 25 70Z" fill="#F28444"/>
  </svg>
  <div class="brand-mini"><span class="dot"></span>Dr AVance</div><div class="rule"></div><div class="page-no">04</div>
</section>

<!-- Slide 5: phase 3 -->
<section class="slide s5">
  <svg class="backdrop" viewBox="0 0 548 308" aria-hidden="true">
    <defs><linearGradient id="band5" x1="0" x2="1"><stop offset="0" stop-color="#0f0f2a"/><stop offset="1" stop-color="#6c68b2"/></linearGradient></defs>
    <path d="M0 0H548V137C450 180 300 176 180 162C100 152 40 160 0 172Z" fill="url(#band5)"/>
    <polyline points="60,148 200,158 330,175 470,180" fill="none" stroke="#F28444" stroke-width="12"/>
  </svg>
  <h2 class="phase-title">PHASE 3: EXPERT EXECUTION</h2>
  <p class="exec-sub" style="top:44px">Where Science Meets Service</p>
  <p class="exec-sub" style="top:68px">Our specialized team begins the transformation process:</p>
  <div class="pill" style="left:31px;top:83px"><span class="cap">01</span>In-depth research and analysis</div>
  <div class="pill" style="left:159px;top:95px"><span class="cap">02</span>Content development &amp; refinement</div>
  <div class="pill" style="left:288px;top:120px"><span class="cap">03</span>Data interpretation &amp; visualization</div>
  <div class="pill" style="left:417px;top:136px;height:150px;font-size:11px;line-height:19px"><span class="cap">04</span>Plain language translation of complex health information</div>
  <div class="brand-mini"><span class="dot"></span>Dr AVance</div><div class="rule"></div><div class="page-no">05</div>
</section>

<!-- Slide 6: phase 4 -->
<section class="slide s6">
  <svg class="backdrop" viewBox="0 0 548 308" aria-hidden="true">
    <defs><linearGradient id="band6" x1="0" x2="1"><stop offset="0" stop-color="#0f0f2a"/><stop offset="1" stop-color="#6c68b2"/></linearGradient></defs>
    <path d="M0 0H548V45C450 85 330 80 230 74C150 70 70 66 0 80Z" fill="url(#band6)"/>
    <path d="M25 70C120 52 230 66 330 78C420 88 480 80 510 65C470 95 400 100 320 95C220 89 120 74 25 70Z" fill="#F28444"/>
  </svg>
  <h2 class="phase-title">PHASE 4: COLLABORATIVE REFINEMENT</h2>
  <p class="subtitle" style="top:115px">Ensuring Perfect Alignment</p>
  <div class="card dark" style="left:27px;top:155px;height:92px;font-size:9.5px;line-height:17px"><span class="badge">01</span>Ensuring Perfect Alignment</div>
  <div class="card mid" style="left:156px;top:155px;height:92px"><span class="badge">02</span>Presentation of initial frameworks</div>
  <div class="card dark" style="left:284px;top:155px;height:92px"><span class="badge">03</span>Custom-tailored solution design</div>
  <div class="card mid" style="left:412px;top:155px;height:92px"><span class="badge">04</span>Clear roadmap development with defined milestones</div>
  <div class="brand-mini"><span class="dot"></span>Dr AVance</div><div class="rule"></div><div class="page-no">06</div>
</section>

</body>
</html>
```